Webdesign für Steuerberaterin
Zielgruppe
Ich bin Steuerberaterin. Meine Zielgruppe sind sowohl Privatpersonen als auch Unternehmer sowie Männer und Frauen.
Aufgabenstellung
Bitte mein Logo und Foto mit berücksichtigen. Ich möchte keine Website, auf der alle 'Reiter' als eine Seite von oben nach unten durchlaufen. Sondern wirklich einzelne, voneinander getrennte Seiten.

```html
<!DOCTYPE html>
<html lang="de">
<head>
<meta charset="utf-8">
<title>Maren Brodtke – Steuerberaterin</title>
<link rel="stylesheet" href="https://fonts.googleapis.com/css2?family=Crimson+Text&family=PT+Sans:wght@400;700&display=swap">
<style>
  :root {
    --sidebar: #1b191e;
    --page: #ffffff;
    --gold: #b08a2e;
    --gold-nav: #c9a02f;
    --gold-band-top: #dcbb3c;
    --gold-band-bottom: #c9a12f;
    --text: #555558;
    --text-strong: #4a4a4d;
    --photo-light: #f1f1f1;
    --photo-mid: #d9d6d2;
  }
  * { margin: 0; padding: 0; box-sizing: border-box; }
  html, body { width: 1200px; height: 960px; overflow: hidden; background: var(--page); }
  .site { position: relative; width: 1200px; height: 960px; font-family: "PT Sans", sans-serif; }

  .sidebar { position: absolute; left: 0; top: 0; width: 307px; height: 933px; background: var(--sidebar); }

  .main-nav { position: absolute; left: 79px; top: 0; }
  .main-nav a {
    position: absolute; left: 0; white-space: nowrap;
    color: var(--gold-nav); font-size: 15px; text-decoration: none;
  }

  .portrait {
    position: absolute; left: 181px; top: 130px; width: 401px; height: 288px;
    background: radial-gradient(ellipse at 55% 45%, var(--photo-light) 0%, var(--photo-mid) 100%);
  }

  .brand-box {
    position: absolute; left: 183px; top: 495px; width: 125px; height: 139px;
    background: var(--page);
    display: flex; align-items: center; justify-content: center; gap: 6px;
  }
  .brand-mark { width: 9px; height: 9px; border-radius: 50%; background: var(--gold); }
  .brand-name { font-family: "PT Sans", sans-serif; font-size: 13px; color: var(--gold); }

  .welcome { position: absolute; left: 615px; top: 0; width: 560px; text-align: center; color: var(--text); }
  .welcome-title {
    position: absolute; left: 0; top: 82px; width: 100%;
    font-family: "Crimson Text", serif; font-weight: 400; font-size: 25px; color: var(--gold);
  }
  .welcome-rule { position: absolute; left: 24px; top: 132px; width: 514px; height: 2px; background: var(--gold); }
  .welcome-lead {
    position: absolute; left: 0; top: 165px; width: 100%;
    font-weight: 700; font-size: 16.5px; color: var(--text-strong);
  }
  .welcome-text { position: absolute; left: 0; width: 100%; font-size: 16.5px; line-height: 21.7px; }
  .welcome-text.first { top: 214px; }
  .welcome-text.second { top: 353px; }
  .welcome-text.third { top: 423px; }

  .footer-band {
    position: absolute; left: 0; top: 933px; width: 1200px; height: 27px;
    background: linear-gradient(var(--gold-band-top), var(--gold-band-bottom));
  }
</style>
</head>
<body>
<div class="site">
  <aside class="sidebar">
    <nav class="main-nav">
      <a href="#" style="top:266px">Über mich</a>
      <a href="#" style="top:309px;left:1px">Leistungen</a>
      <a href="#" style="top:355px">Kontakt</a>
      <a href="#" style="top:400px">Impressum</a>
    </nav>
  </aside>

  <div class="portrait" role="img" aria-label="Porträtfoto der Steuerberaterin vor heller Steinwand"></div>

  <div class="brand-box">
    <span class="brand-mark"></span>
    <span class="brand-name">Maren Brodtke</span>
  </div>

  <main class="welcome">
    <h1 class="welcome-title">Schön, dass Sie da sind</h1>
    <div class="welcome-rule"></div>
    <p class="welcome-lead">Ich freue mich, dass Sie den Weg zu mir gefunden haben!</p>
    <p class="welcome-text first">Sie sind bei mir genau richtig:<br>Egal, ob Sie Privatperson sind, die Ihre Einkommensteuer-Erklärung<br>in vertrauensvolle Hände geben möchte,<br>oder Unternehmer, der sich z.B. das „Rundum-Sorglos-Paket“<br>mit Buchführung, Jahresabschluss und Steuererklärungen wünscht.</p>
    <p class="welcome-text second">Schauen Sie sich hier gerne um und melden Sie sich bei mir – ich bin bei jedem<br>steuerlichen Thema gerne Ihr kompetenter und zuverlässiger Ansprechpartner.</p>
    <p class="welcome-text third">Für mich ist es eine Selbstverständlichkeit,<br>dass ich auch nach mehr als 12 Jahren Berufserfahrung<br>durch permanente Fortbildungen immer auf dem aktuellsten Stand<br>der relevanten Gesetze und Verordnungen bin.<br>Nur so kann ich Sie bestmöglich beraten.</p>
  </main>

  <div class="footer-band"></div>
</div>
</body>
</html>
```